Web Design Project

We are an IT System Integrator. We provide Korvin 450 ERP System, CRM etc. We also provide hardware, networking servicing. Please look at www.zolvantix.com.sg. They provide the same service as us. We like to redesign our web site. I will attached the color that I prefer for reference.

Our website is www.tadurk.com.sg.  It has been created about 14 years ago.  We are trying to revamp it with a new look and information.   The new website must be informative, fast.    I have attached an attachment which show the color that I prefer(brownish golden).   

Our competitor (www.zolvantix.com) is carrying the same trade as us.  They have all the informations In their website that we will like to have.  Therefore I recommend you to take a look at my competitor website and have a better   
understanding on the kind of information I would like to have for my new website.

This project is guarantee to the person with the best design.  We can have it guarantee.

Target Market(s)

Corporate and companies

Industry/Entity Type

Hardware

```html
<!DOCTYPE html>
<html lang="en">
<head>
<meta charset="utf-8">
<title>Tadurk Information Systems Pte Ltd</title>
<link href="https://fonts.googleapis.com/css2?family=Open+Sans:ital,wght@0,400;0,600;0,700;1,400&family=Lora:ital,wght@0,700;1,400&display=swap" rel="stylesheet">
<style>
:root{
  --gold:#b07a2e;
  --gold-light:#d5a55a;
  --ink:#4a4a4a;
  --muted:#6b6b6b;
  --nav:#555;
  --hero-text:#2e2f93;
  --band:#3b85c9;
  --band-dark:#2f74b6;
  --heading:#3b3ba3;
  --footer:#0f3d5c;
  --footer-line:#2d5b7a;
  --wave:#1a7fd0;
  --navy:#0c1f6b;
}
*{box-sizing:border-box;margin:0;padding:0}
html,body{width:1029px;height:1200px;overflow:hidden;background:#fff}
body{position:relative;font-family:"Open Sans",Arial,sans-serif;color:var(--ink)}
.abs{position:absolute}
.top-rule{left:0;top:0;width:1029px;height:3px;background:#a9773a}
.brand{left:109px;top:22px;display:flex;align-items:center;gap:10px}
.brand-dot{width:58px;height:58px;border-radius:50%;background:var(--gold-light)}
.brand-name{color:var(--gold);font-weight:600;font-size:11.5px;line-height:23px;letter-spacing:.3px}
.main-nav{left:416px;top:4px;display:flex;height:41px}
.main-nav a{display:flex;align-items:center;padding:0 12px;font-size:11px;font-weight:600;color:var(--nav);text-decoration:none;border-right:1px solid #e2e2e2;letter-spacing:.2px}
.main-nav a:last-child{border-right:0}
.main-nav a.active{background:linear-gradient(#cda15c,#a87636);color:#fff;padding:0 8px;height:41px}
.sub-nav{right:112px;top:85px;display:flex;font-size:9px;color:#777}
.sub-nav span{padding:0 12px}
.sub-nav span+span{border-left:1px solid #aaa}
.sub-nav span:last-child{padding-right:0}
.hero{left:0;top:105px;width:1029px;height:284px;background:linear-gradient(#cfd7ec,#d9e4f3 55%,#bfe4f5)}
.hero-photo{left:109px;top:1px;width:500px;height:283px;background:linear-gradient(135deg,#c9cdd8,#9ea6b5 60%,#6e7380);border-radius:0 140px 0 0}
.hero-copy{left:515px;top:29px;width:410px;font-family:"Lora",Georgia,serif;font-style:italic;font-size:17px;line-height:29.5px;color:var(--hero-text)}
.btn-learn{left:544px;top:195px;width:122px;height:32px;border-radius:4px;background:linear-gradient(#3fa2e8,#1373c8);color:#fff;font-family:"Lora",Georgia,serif;font-size:17px;display:flex;align-items:center;justify-content:center}
.dots{left:561px;top:266px;display:flex;gap:6px;align-items:center}
.dots i{width:7px;height:7px;border-radius:50%;background:#2a2a3a;display:block}
.dots i.on{width:11px;height:11px;background:#2f86d3;border:2px solid #fff;box-shadow:0 0 0 1px #2f86d3}
.services{left:0;top:389px;width:1029px;height:222px;background:var(--band)}
.svc{position:absolute;width:270px;height:70px}
.svc-icon{position:absolute;left:0;top:0;width:66px;height:66px;border-radius:50%;background:radial-gradient(#fff 55%,#dce8f4);box-shadow:0 2px 4px rgba(0,0,0,.2);display:flex;align-items:center;justify-content:center}
.svc h3{position:absolute;left:77px;font-size:11.5px;font-weight:600;color:#fff;line-height:14px}
.svc p{position:absolute;left:79px;font-size:9.5px;color:#e3eefa;line-height:11.5px}
.arrow{width:28px;height:28px;border:1.5px solid #fff;border-radius:50%;display:flex;align-items:center;justify-content:center}
.content{left:0;top:611px;width:1029px;height:330px;background:linear-gradient(#f0f0f0,#fff 60%)}
.h-sect{font-size:13.5px;font-weight:600;color:var(--heading);letter-spacing:.1px}
.welcome-img{left:115px;top:666px;width:245px;height:93px;border:1px solid #ccc;background:#fff;padding:3px}
.welcome-img div{width:100%;height:100%;background:linear-gradient(90deg,#e8d3d3,#c9d6ec 35%,#cfe8c9 65%,#f0e6c3)}
.welcome-text{left:114px;top:772px;width:331px;font-size:10.3px;line-height:16px;color:var(--muted);text-align:justify;letter-spacing:.15px}
.read-more{left:388px;top:890px;font-size:10.5px;color:#2d6fc1;text-decoration:underline}
.clients{left:482px;top:666px;width:438px;height:246px;border:1px solid #ccc;background:#fff}
.client{position:absolute;font-weight:700;font-size:13px;text-align:center;line-height:15px;transform:translate(-50%,-50%);white-space:nowrap}
.footer{left:0;top:930px;width:1029px;height:230px}
.f-head{font-family:"Lora",Georgia,serif;font-weight:700;font-size:14px;color:#fff}
.f-rule{width:1px;height:127px;background:var(--footer-line);top:1008px}
.quick{left:130px;top:1024px;list-style:none;font-size:10.5px;line-height:19px;color:#fff}
.addr{left:276px;top:1024px;font-size:10px;line-height:14px;color:#fff}
.contact-line{left:278px;display:flex;align-items:center;gap:12px;font-size:11.5px;font-weight:700;color:#fff}
.quote{left:520px;top:1028px;width:172px;font-size:10.3px;font-style:italic;line-height:14.2px;color:#fff;text-indent:12px}
.quote-name{left:600px;top:1114px;width:90px;text-align:right;font-size:9.5px;font-weight:700;color:#fff}
.social{top:1026px;width:26px;height:24px;border-radius:3px;display:flex;align-items:center;justify-content:center;font-size:7px;font-weight:600;color:#fff}
.copyright{left:0;top:1160px;width:1029px;height:40px;background:#050505;color:#fff;font-size:10px;display:flex;align-items:center;justify-content:center}
</style>
</head>
<body>
<div class="abs top-rule"></div>

<header>
  <div class="abs brand">
    <span class="brand-dot"></span>
    <div class="brand-name">TADURK<br>INFORMATION<br>SYSTEMS PTE LTD</div>
  </div>
  <nav class="abs main-nav">
    <a class="active">COMPANY</a><a>PRODUCTS</a><a>LEDGRA</a><a>SERVICES</a><a>CLIENTELE</a><a>CAREERS</a><a>INFOBIN</a>
  </nav>
  <div class="abs sub-nav">
    <span>HOME</span><span>SITEMAP</span><span>LOG INCIDENT</span><span>ENQUIRY</span><span>CONTACT</span><span>CLIENT SUPPORT</span>
  </div>
</header>

<section class="abs hero">
  <div class="abs hero-photo" role="img" aria-label="Photo of a smiling business team in front of a jigsaw globe"></div>
  <p class="abs hero-copy">A unique combination of both accounting and technical expertise so as to implement sound,reliable LEDGRA Accounting Software and Networking systems, specifically tailored to individual business needs.</p>
  <div class="abs btn-learn">Learn more</div>
  <div class="abs dots"><i class="on"></i><i></i><i></i></div>
</section>

<section class="abs services">
  <div class="abs arrow" style="left:66px;top:97px"><svg width="10" height="14" viewBox="0 0 10 14"><path d="M8 1 2 7l6 6" fill="none" stroke="#fff" stroke-width="1.6"/></svg></div>
  <div class="abs arrow" style="left:932px;top:97px"><svg width="10" height="14" viewBox="0 0 10 14"><path d="M2 1l6 6-6 6" fill="none" stroke="#fff" stroke-width="1.6"/></svg></div>

  <div class="svc" style="left:108px;top:31px">
    <div class="svc-icon"><svg width="30" height="34" viewBox="0 0 30 34"><g fill="#3b85c9"><ellipse cx="15" cy="5" rx="14" ry="4.5"/><path d="M1 8c0 6 28 6 28 0v6c0 6-28 6-28 0z"/><path d="M1 17c0 6 28 6 28 0v6c0 6-28 6-28 0z"/><path d="M1 26c0 6 28 6 28 0v3c0 6-28 6-28 0z"/></g></svg></div>
    <h3 style="top:6px">Orvane Software and Technology<br>Reseller</h3>
    <p style="top:37px">Lorem ipsum dolor sit amet, onsectetuer</p>
  </div>
  <div class="svc" style="left:388px;top:31px">
    <div class="svc-icon"><svg width="34" height="30" viewBox="0 0 34 30"><g fill="none" stroke="#3b85c9" stroke-width="4"><path d="M5 14a12 10 0 0 1 22-5"/><path d="M29 16a12 10 0 0 1-22 5"/></g><path d="M23 3l8 1-2 8z M11 27l-8-1 2-8z" fill="#3b85c9"/></svg></div>
    <h3 style="top:6px">Migrations &amp; Upgrades to the 9's</h3>
    <p style="top:21px">Lorem ipsum dolor sit amet, onsectetuer<br>adipiscing elit, sed diam nonummy</p>
  </div>
  <div class="svc" style="left:673px;top:31px">
    <div class="svc-icon"><svg width="36" height="34" viewBox="0 0 36 34"><rect x="2" y="3" width="26" height="28" fill="#3b6fb8"/><g stroke="#fff" stroke-width="1.5"><path d="M6 9h18M6 13h18M6 17h12"/></g><path d="M12 20l6 7 15-19" fill="none" stroke="#6cc137" stroke-width="4"/></svg></div>
    <h3 style="top:1px">Report Development</h3>
    <p style="top:16px">Lorem ipsum dolor sit amet, onsectetuer<br>adipiscing elit, sed diam nonummy</p>
  </div>

  <div class="svc" style="left:108px;top:125px">
    <div class="svc-icon"><svg width="30" height="30" viewBox="0 0 30 30"><g fill="#3b85c9"><rect x="2" y="2" width="11" height="11" rx="2"/><rect x="17" y="2" width="11" height="11" rx="2"/><rect x="2" y="17" width="26" height="11" rx="2"/></g></svg></div>
    <h3 style="top:8px">Consulting Services for Stratum&reg;<br>and StratumOne&reg;</h3>
    <p style="top:39px">Lorem ipsum dolor sit amet, onsectetuer</p>
  </div>
  <div class="svc" style="left:388px;top:125px">
    <div class="svc-icon"><svg width="30" height="34" viewBox="0 0 30 34"><path d="M3 2h14l7 7v10M3 2v29h14" fill="none" stroke="#3b85c9" stroke-width="3.5"/><path d="M22 20v12M16 26h12" stroke="#3b85c9" stroke-width="4"/></svg></div>
    <h3 style="top:8px">Custom Applications Development</h3>
    <p style="top:25px">Lorem ipsum dolor sit amet, onsectetuer<br>adipiscing elit, sed diam nonummy</p>
  </div>
  <div class="svc" style="left:673px;top:125px">
    <div class="svc-icon"><svg width="32" height="32" viewBox="0 0 32 32"><circle cx="16" cy="16" r="10" fill="none" stroke="#3b85c9" stroke-width="5"/><circle cx="16" cy="16" r="3" fill="#3b85c9"/></svg></div>
    <h3 style="top:8px">Technical and CNC</h3>
    <p style="top:25px">Lorem ipsum dolor sit amet, onsectetuer<br>adipiscing elit, sed diam nonummy</p>
  </div>
</section>

<section class="abs content"></section>
<h2 class="abs h-sect" style="left:110px;top:640px">Welcome to Tadurk Information Systems Pte Ltd (TIS)</h2>
<div class="abs welcome-img"><div role="img" aria-label="Illustration of four figures joining coloured puzzle pieces"></div></div>
<p class="abs welcome-text">The principal business activities of TIS are implementing of LEDGRA Accounting software, networking, hardware maintenance and consulting assistance. We also provide Broadband services and Web hosting and designing services. We have the skills and experience to deliver a complete range of implementation services, which includes Local Area Network (LAN), Wide Area Network (WAN) and Communications (Internet and Intranet).</p>
<a class="abs read-more">Read More</a>

<h2 class="abs h-sect" style="left:480px;top:640px">OUR CLIENTS</h2>
<div class="abs clients">
  <span class="client" style="left:55px;top:40px;color:#c8202a">Brightfield<br>Dairy</span>
  <span class="client" style="left:161px;top:40px;color:#c8202a">Halvern</span>
  <span class="client" style="left:276px;top:40px;color:#1c5aa8;font-size:17px">Quenta</span>
  <span class="client" style="left:390px;top:89px;color:#111;font-size:22px">RKV</span>
  <span class="client" style="left:57px;top:110px;color:#1f3f8c">Meadowline<br>Dairy</span>
  <span class="client" style="left:175px;top:110px;color:#d42027">Corvel Dairy</span>
  <span class="client" style="left:290px;top:110px;color:#1c4a9a">Prisa Foods</span>
  <span class="client" style="left:59px;top:196px;color:#1c2f8a">Oskel<br>Farms</span>
  <span class="client" style="left:172px;top:196px;color:#2d7a2a">Tollan Dairy</span>
  <span class="client" style="left:295px;top:196px;color:#c8202a;font-size:15px">Pastora</span>
</div>

<footer class="abs footer">
  <svg class="abs" style="left:0;top:0" width="1029" height="230" viewBox="0 0 1029 230">
    <path d="M0 40C200 -10 420 40 640 50 800 58 920 30 1029 10V230H0Z" fill="var(--footer)"/>
    <path d="M0 40C150 -5 330 15 520 40 700 60 880 45 1029 8V18C880 60 700 72 520 50 330 25 150 12 0 50Z" fill="var(--wave)"/>
    <path d="M30 48C120 25 220 28 290 40 200 32 110 38 30 48Z" fill="var(--wave)"/>
    <path d="M525 21C700 32 860 25 1029 10 880 35 720 42 525 21Z" fill="var(--navy)"/>
  </svg>
</footer>

<h3 class="abs f-head" style="left:124px;top:994px">Quick Links</h3>
<h3 class="abs f-head" style="left:274px;top:994px">Contact Details</h3>
<h3 class="abs f-head" style="left:528px;top:994px">Client's Testimonial</h3>
<h3 class="abs f-head" style="left:764px;top:994px">Follow Us</h3>
<div class="abs f-rule" style="left:238px"></div>
<div class="abs f-rule" style="left:484px"></div>
<div class="abs f-rule" style="left:722px"></div>

<ul class="abs quick">
  <li>Company</li><li>Products</li><li>LEDGRA</li><li>Services</li><li>Clientele</li><li>Careers</li><li>Infobin</li>
</ul>
<address class="abs addr" style="font-style:normal">1250 Jalan Kembang Raya<br>#05-12 Tech-Hub@Kembang<br>Singapore 160382</address>
<div class="abs contact-line" style="top:1074px">
  <svg width="16" height="16" viewBox="0 0 16 16"><path d="M3 1l3 3-2 2c1 2 3 4 5 5l2-2 3 3-2 3C7 15 1 9 1 3z" fill="#fff"/></svg>
  <span>(065) 6408-1135</span>
</div>
<div class="abs contact-line" style="top:1098px">
  <svg width="18" height="13" viewBox="0 0 18 13"><rect x="1" y="1" width="16" height="11" fill="none" stroke="#fff" stroke-width="1.5"/><path d="M1 1l8 6 8-6M1 12l6-5M17 12l-6-5" fill="none" stroke="#fff" stroke-width="1.3"/></svg>
  <span>sales@tadurk.com.sg</span>
</div>
<p class="abs quote">&ldquo; Lorem ipsum dolor sit amet, consectetuer adipiscing elit, sed diam nonummy nibh euismod tincidunt ut laoreet dolore magna aliquam erat volutpat. &rdquo;</p>
<div class="abs quote-name">- DORIAN WELLES</div>
<div class="abs social" style="left:765px;background:#3a62a8">Folio</div>
<div class="abs social" style="left:802px;background:#3fa6dd">Chirp</div>
<div class="abs social" style="left:839px;background:#1f74b0">Nexa</div>

<div class="abs copyright">&copy; Copyrights 2013. Tadurk Information Systems. All Rights Reserved.</div>
</body>
</html>
```